Marwick Law Letterhead

We need a new letterhead design for a Law Firm. The address for the law firm is 1475 Calloway Street, Suite 210, Houston, Texas 77041. Phone Number: 832-361-9027; Fax Number: 832-614-7359. The logo is uploaded to the project.

```html
<!DOCTYPE html>
<html lang="en">
<head>
<meta charset="utf-8">
<title>Marwick Law Letterhead</title>
<link href="https://fonts.googleapis.com/css2?family=Montserrat:wght@400;500;600&display=swap" rel="stylesheet">
<style>
  :root {
    --backdrop: #e9e9eb;
    --paper: #ffffff;
    --ink: #1f1f1f;
    --navy: #1e2f63;
    --red-light: #e0161f;
    --red-dark: #7a0010;
    --sig-tone: #ececec;
  }
  * { box-sizing: border-box; margin: 0; padding: 0; }
  html, body {
    width: 1200px; height: 960px; overflow: hidden;
    background: var(--backdrop);
    font-family: "Montserrat", Arial, sans-serif;
    color: var(--ink);
  }
  .letterhead {
    position: absolute; left: 282px; top: 30px;
    width: 636px; height: 900px;
    background: var(--paper);
    box-shadow: 0 2px 10px rgba(0,0,0,0.12);
    overflow: hidden;
  }
  .contact-panel {
    position: absolute; top: 20px; right: 0;
    width: 250px; height: 150px;
    background: linear-gradient(110deg, var(--red-light), var(--red-dark));
    color: #fff;
    font-size: 10.5px; line-height: 1.45;
    padding: 30px 22px 0 62px;
  }
  .contact-panel .phone-row { display: flex; align-items: center; gap: 6px; margin-top: 4px; }
  .contact-panel .phone-row + .phone-row { margin-top: 0; }
  .contact-panel svg { width: 10px; height: 10px; fill: #fff; }
  .brand {
    position: absolute; left: 46px; top: 108px;
    display: flex; align-items: center; gap: 10px;
  }
  .brand-dot { width: 26px; height: 26px; border-radius: 50%; background: var(--red-light); }
  .brand-name {
    font-size: 24px; font-weight: 600; color: var(--navy);
    letter-spacing: 0.5px;
  }
  .letter-content {
    position: absolute; left: 60px; top: 200px; width: 510px;
    display: flex; flex-direction: column;
  }
  .recipient {
    font-size: 11.5px; line-height: 1.45;
    margin-bottom: 12px;
  }
  .letter-body {
    font-size: 11px; line-height: 1.5;
  }
  .letter-body p { margin-bottom: 12px; }
  .letter-body p:last-child { margin-bottom: 0; }
  .closing {
    margin-top: 18px;
    font-size: 12.5px; font-weight: 500;
  }
  .signature {
    margin: 6px 0 0 10px;
    width: 120px; height: 40px;
    background: var(--sig-tone); border-radius: 3px;
  }
</style>
</head>
<body>
  <div class="letterhead">
    <div class="contact-panel">
      <div class="address">1475 Calloway Street,<br>Suite 210, Houston,<br>Texas 77041</div>
      <div class="phone-row">
        <svg viewBox="0 0 24 24" aria-hidden="true"><path d="M6.6 10.8a15.1 15.1 0 0 0 6.6 6.6l2.2-2.2c.3-.3.7-.4 1-.2 1.1.4 2.3.6 3.6.6.6 0 1 .4 1 1V20c0 .6-.4 1-1 1A17 17 0 0 1 3 4c0-.6.4-1 1-1h3.5c.6 0 1 .4 1 1 0 1.3.2 2.5.6 3.6.1.3 0 .7-.2 1z"/></svg>
        <span>832-361-9027</span>
      </div>
      <div class="phone-row">
        <svg viewBox="0 0 24 24" aria-hidden="true"><path d="M6 3h10v5H6zM4 9h16a2 2 0 0 1 2 2v6h-4v4H6v-4H2v-6a2 2 0 0 1 2-2zm4 7v3h8v-3z"/></svg>
        <span>832-614-7359</span>
      </div>
    </div>

    <div class="brand">
      <span class="brand-dot"></span>
      <span class="brand-name">Marwick Law</span>
    </div>

    <div class="letter-content">
      <div class="recipient">
        Mr/s<br>First Name and Last Name<br>Company Name<br>Address
      </div>

      <div class="letter-body">
        <p>Lorem ipsum dolor sit amet,consectetur adipiscing sed do eiusmod tempor incididunt laboreet dolore magna aliqua.Ut enim ad minim.veniam, quis nostrud exercitation ullamco laboris nisi ut aliquip exea commodo consequat.Lorem ipsum dolor sit amet,consectetur adipiscing sed do eiusmod tempor incididunt.labore et dolore magna aliqua. Ut enim</p>
        <p>Lorem ipsum dolor sit amet, consectetur adipiscing sed do eiusmod tempor incididunt labore et dolore magna aliqua. Ut enim ad minim veniam, quis nostrud exercitation ullamco laboris nisi ut aliquip exea commodo consequat.Duis aute irure dolor in reprehenderit in voluptate velit esse cillum irure dolor in reprehenderit in voluptate velit esse irure</p>
        <p>Lorem ipsum dolor sit amet, consectetur adipiscing sed do eiusmod tempor incididunt labore et dolore magna aliqua. consequat. Duis aute irure dolor in.reprehenderit in voluptate velit esse cillum dolore eu fugiat nulla pariatur. Excepteur sint occaecat cupidatat non proident, sunt in culpa qui officia deserunt mollit,</p>
        <p>Lorem ipsum dolor sit amet, consectetur adipiscing sed do eiusmod tempor incididunt labore et dolore magna aliqua. Ut enim Lorem ipsum dolor sit amet, consectetur adipiscing sed do eiusmod tempor incididunt labore et dolore magna aliqua. Ut enim Lorem ipsum aliqua.ipsum</p>
        <p>Lorem ipsum dolor sit amet, consectetur adipiscing sed do eiusmod tempor incididunt labore et dolore magna aliqua. Ut enim ad minim veniam, quis nostrud exercitation ullamco laboris nisi ut aliquip exea commodo consequat.Duis aute irure dolor in reprehenderit in voluptate velit esse cillum irure dolor in reprehenderit in voluptate velit esse irure</p>
        <p>Lorem ipsum dolor sit amet, consectetur adipiscing sed do eiusmod tempor incididunt labore et dolore magna aliqua. Ut enim ad minim veniam, quis nostrud exercitation ullamco laboris nisi ut aliquip exea commodo consequat.Duis aute irure dolor in reprehenderit in voluptate velit esse cillum irure dolor in reprehenderit in voluptate velit esse irure</p>
      </div>

      <div class="closing">Regards</div>
      <div class="signature" role="img" aria-label="Handwritten signature of Harlan"></div>
    </div>
  </div>
</body>
</html>
```